Business Card for my New Brokerage

Looking to get a business card design for my new Real Estate Brokerage.
I want it with Picture, Phone Number, Email, Website, Office Address
Name and Designation. Please add logo too.

Target Market(s)

Real Estate Investors or Home Buyers

Industry/Entity Type

Real Estate

Contact Information for Business Card

Name, Email, Phone Number, website, email, office address

Colors
EB3D1F
EC4F4E
F09395
F8D3D4
FCEDEE

Requirements
Must have
• Minimalistic, Clean, Modern, Photo
Nice to have
• White and Red Colors

```html
<!DOCTYPE html>
<html lang="en">
<head>
<meta charset="utf-8">
<title>Ember Realty Inc — Business Card</title>
<link href="https://fonts.googleapis.com/css2?family=Montserrat:wght@500;700;800&display=swap" rel="stylesheet">
<style>
  :root {
    --brand-red: #e2382a;
    --brand-red-dark: #c92c20;
    --ink: #2a2a2a;
    --paper: #ffffff;
    --backdrop: #c4c7c9;
    --photo-light: #d8d2cc;
    --photo-dark: #2f3a50;
  }
  * { margin: 0; padding: 0; box-sizing: border-box; }
  html, body {
    width: 1187px; height: 1200px; overflow: hidden;
    background: var(--backdrop);
    font-family: "Montserrat", sans-serif;
  }
  .card {
    position: absolute; left: 214px; width: 760px; height: 433px; overflow: hidden;
  }
  .card-front { top: 120px; background: var(--brand-red); }
  .card-back { top: 642px; background: var(--paper); }
  .text { position: absolute; line-height: 1; white-space: nowrap; }

  /* front */
  .skyline {
    position: absolute; left: 0; right: 0; bottom: 0; height: 165px;
    background: linear-gradient(to bottom, rgba(201,44,32,0) 0%, var(--brand-red-dark) 35%, var(--brand-red-dark) 100%);
  }
  .front-name {
    left: 0; right: 0; top: 174px; text-align: center;
    font-size: 80px; font-weight: 700; color: var(--paper); letter-spacing: 1px;
  }
  .front-sub {
    left: 0; right: 0; top: 259px; text-align: center;
    font-size: 24px; font-weight: 500; color: var(--paper); letter-spacing: 5px;
  }
  .front-url {
    left: 0; right: 0; top: 386px; text-align: center;
    font-size: 17px; font-weight: 500; color: var(--paper); letter-spacing: 1.5px;
  }

  /* back */
  .back-name {
    left: 50px; top: 52px; font-size: 60px; font-weight: 700; color: var(--brand-red); letter-spacing: 1px;
  }
  .back-sub {
    left: 96px; top: 108px; font-size: 19px; font-weight: 500; color: var(--brand-red); letter-spacing: 4px;
  }
  .name-band {
    position: absolute; left: 0; right: 0; top: 166px; height: 80px; background: var(--brand-red);
  }
  .agent-name { left: 51px; top: 183px; font-size: 30px; font-weight: 800; color: var(--paper); letter-spacing: 1px; }
  .agent-title { left: 50px; top: 220px; font-size: 17px; font-weight: 500; color: var(--paper); letter-spacing: .5px; }
  .address { left: 51px; font-size: 17px; font-weight: 500; color: var(--ink); letter-spacing: .8px; }
  .address-1 { top: 260px; }
  .address-2 { top: 287px; }
  .divider { position: absolute; left: 52px; top: 310px; width: 57px; height: 3px; background: var(--brand-red); }
  .contact { position: absolute; left: 51px; display: flex; align-items: center; gap: 8px;
    font-size: 17px; font-weight: 500; color: var(--ink); letter-spacing: .8px; line-height: 1; }
  .contact svg { width: 14px; height: 14px; fill: var(--brand-red); flex: none; }
  .contact-phone { top: 323px; }
  .contact-email { top: 352px; }
  .contact-web { top: 381px; }
  .portrait {
    position: absolute; left: 403px; top: 33px; width: 357px; height: 400px;
    background: linear-gradient(to bottom, var(--photo-light) 0%, #8d7f78 40%, var(--photo-dark) 75%);
  }
</style>
</head>
<body>

<section class="card card-front">
  <div class="skyline" role="img" aria-label="City skyline silhouette in darker red"></div>
  <div class="text front-name">EMBER</div>
  <div class="text front-sub">REALTY INC</div>
  <div class="text front-url">www.emberrealtyinc.com</div>
</section>

<section class="card card-back">
  <div class="text back-name">EMBER</div>
  <div class="text back-sub">REALTY INC</div>

  <div class="name-band"></div>
  <div class="portrait" role="img" aria-label="Portrait photo of the broker in a navy suit and white shirt"></div>

  <div class="text agent-name">DANIEL REYES</div>
  <div class="text agent-title">Broker Associate</div>

  <div class="text address address-1">204 Harbor Point Complex</div>
  <div class="text address address-2">Westbridge Business Park</div>
  <div class="divider"></div>

  <div class="contact contact-phone">
    <svg viewBox="0 0 24 24" aria-hidden="true"><path d="M6.6 10.8a15.1 15.1 0 0 0 6.6 6.6l2.2-2.2c.3-.3.7-.4 1-.2 1.1.4 2.3.6 3.6.6.6 0 1 .4 1 1V20c0 .6-.4 1-1 1A17 17 0 0 1 3 4c0-.6.4-1 1-1h3.5c.6 0 1 .4 1 1 0 1.3.2 2.5.6 3.6.1.3 0 .7-.2 1z"/></svg>
    <span>555-014-2290</span>
  </div>
  <div class="contact contact-email">
    <svg viewBox="0 0 24 24" aria-hidden="true"><path d="M2 5h20v14H2z M3.5 6.5v.4l8.5 6 8.5-6v-.4z" fill-rule="evenodd"/></svg>
    <span>info@emberrealtyinc.com</span>
  </div>
  <div class="contact contact-web">
    <svg viewBox="0 0 24 24" aria-hidden="true"><path d="M12 2a10 10 0 1 0 0 20 10 10 0 0 0 0-20zm0 2c.9 1.2 1.6 2.9 1.9 5h-3.8c.3-2.1 1-3.8 1.9-5zM9.7 4.4C9.1 5.7 8.7 7.3 8.5 9H5.1a8 8 0 0 1 4.6-4.6zm4.6 0A8 8 0 0 1 18.9 9h-3.4c-.2-1.7-.6-3.3-1.2-4.6zM4.3 11h4.1v2H4.3a8 8 0 0 1 0-2zm6 0h3.8v2h-3.8zm5.5 0h4a8 8 0 0 1 0 2h-4zM5.1 15h3.4c.2 1.7.6 3.3 1.2 4.6A8 8 0 0 1 5.1 15zm5 0h3.8c-.3 2.1-1 3.8-1.9 5-.9-1.2-1.6-2.9-1.9-5zm5.4 0h3.4a8 8 0 0 1-4.6 4.6c.6-1.3 1-2.9 1.2-4.6z"/></svg>
    <span>www.emberrealtyinc.com</span>
  </div>
</section>

</body>
</html>
```